Mental Health Clinic Website

website for a mental health clinic. two files describing the website are attached, in case of conflicting info the word document is priority.

Target Market(s)

Ohio / Pennsylvania residents

Industry/Entity Type

Health Care

Coding

Coded - Design and coding required

Number of Pages Required

5+ page

Requirements
Must have
• see attached

```html
<!DOCTYPE html>
<html lang="en">
<head>
<meta charset="utf-8">
<title>Dr Halvorsen Serenity Center</title>
<link href="https://fonts.googleapis.com/css2?family=Montserrat:wght@400;600;700;800&family=Open+Sans:wght@400;600;700&display=swap" rel="stylesheet">
<style>
:root{
  --blue:#1c5ba6;
  --red:#e1262c;
  --orange:#f26b1d;
  --green:#4f9a34;
  --ink:#333;
  --grey:#e6e6e6;
  --dark:#141414;
  --white:#fff;
}
*{margin:0;padding:0;box-sizing:border-box}
html,body{width:1200px;height:4615px;overflow:hidden}
body{font-family:"Open Sans",sans-serif;color:var(--ink);background:var(--white);position:relative}
section,header,footer{position:absolute;left:0;width:1200px}
.abs{position:absolute}
h2.title{font-family:"Montserrat",sans-serif;font-weight:800;color:var(--blue);font-size:36px;letter-spacing:1px;text-align:center}
.eyebrow{font-family:"Montserrat",sans-serif;font-weight:700;color:var(--red);font-size:30px;text-align:center}
.wave{display:block;margin:10px auto 0}
.btn{display:inline-block;background:var(--orange);color:var(--white);font-family:"Montserrat",sans-serif;font-weight:700;font-size:15px;letter-spacing:1px;clip-path:polygon(6% 0,100% 0,94% 100%,0 100%);text-align:center}

/* hero */
.hero{top:0;height:665px;overflow:hidden}
.hero-bg{position:absolute;inset:0;background:linear-gradient(180deg,#5d6f86 0%,#8f8a84 30%,#d99b55 48%,#6f7a52 62%,#2f3a2a 100%)}
.nav{position:absolute;top:40px;left:308px;width:584px;height:32px;background:var(--white);clip-path:polygon(4% 0,100% 0,96% 100%,0 100%);display:flex;justify-content:center;gap:30px;align-items:center;font-family:"Montserrat",sans-serif;font-weight:700;font-size:13px;color:#222}
.hero-mark{position:absolute;top:190px;left:0;width:1200px;text-align:center;color:var(--white);font-family:"Montserrat",sans-serif;font-weight:700;font-size:30px}
.hero-mark .dot{display:block;width:150px;height:150px;border-radius:50%;background:rgba(255,255,255,.18);margin:0 auto 22px}
.hero-name{position:absolute;top:478px;width:1200px;text-align:center;color:var(--white);font-size:20px}
.hero-contact{position:absolute;top:530px;width:1200px;display:flex;justify-content:center;gap:30px;color:var(--white);font-weight:600;font-size:16px;align-items:center;white-space:nowrap}
.hero-contact span{display:flex;align-items:center;gap:10px}
.hero-arrows{position:absolute;top:578px;left:556px;display:flex;gap:8px}
.hero-arrows i{width:38px;height:38px;border:2px solid var(--white);border-radius:50%;display:flex;align-items:center;justify-content:center}

/* welcome */
.welcome{top:665px;height:530px}
.welcome .eyebrow{margin-top:44px}
.welcome p{width:960px;margin:0 auto;text-align:center;font-size:16px;line-height:27px;color:#444}
.welcome p+p{margin-top:27px}
.welcome .intro{margin-top:28px}

/* about */
.about{top:1195px;height:1082px;overflow:hidden}
.about-bg{position:absolute;inset:0;background:linear-gradient(180deg,#bfd8ea 0%,#e9f1f6 30%,#f5efe6 55%,#fff 68%)}
.about .eyebrow{position:absolute;top:55px;width:1200px}
.about h2{position:absolute;top:97px;width:1200px;z-index:2}
.hands{position:absolute;top:135px;left:530px;width:140px;height:130px;border-radius:70px 70px 0 0;background:linear-gradient(180deg,#d9a47a,#b87a52)}
.about-box{position:absolute;top:225px;left:154px;width:892px;height:310px;background:var(--white);text-align:center;padding-top:38px}
.about-box p{font-size:16px;line-height:25px;width:620px;margin:0 auto;color:#333}
.about-box h4{font-size:18px;font-weight:700;margin-top:24px;color:#222}
.langs{margin:20px auto 0;width:450px;height:40px;background:var(--grey);clip-path:polygon(4% 0,100% 0,96% 100%,0 100%);display:flex;justify-content:center;align-items:center;gap:18px;font-weight:700;font-size:14px}
.langs b{width:7px;height:7px;border-radius:50%;background:#aaa}
.team{position:absolute;top:570px;left:148px;display:flex;gap:6px}
.team div{width:175px;height:210px}
.team .active{outline:6px solid var(--orange);outline-offset:-6px;position:relative}
.team .active:after{content:"";position:absolute;bottom:-14px;left:76px;border:12px solid transparent;border-top-color:var(--orange);border-bottom:0}
.member{position:absolute;top:800px;width:1200px;text-align:center}
.member h3{font-family:"Montserrat",sans-serif;font-weight:700;font-size:26px;color:#333}
.member .role{font-size:18px;color:#555;margin-top:4px}
.member p{width:820px;margin:26px auto 0;font-size:14px;line-height:24px;color:#444}
.member .btn{margin-top:28px;width:330px;height:44px;line-height:44px}

/* services */
.services{top:2277px;height:758px;overflow:hidden}
.services-bg{position:absolute;inset:0;background:linear-gradient(180deg,#1b2336 0%,#3a4660 35%,#7d8a8c 60%,#a9a38c 80%,#6a6b55 100%)}
.services h2{position:absolute;top:38px;width:1200px}
.card{position:absolute;background:var(--green);display:flex;flex-direction:column;align-items:center;justify-content:center;color:#222}
.card svg{margin-bottom:28px}
.card .label{background:var(--white);font-family:"Montserrat",sans-serif;font-weight:700;font-size:14px;width:250px;height:44px;line-height:44px;text-align:center;clip-path:polygon(6% 0,100% 0,94% 100%,0 100%);color:#222}
.card.dim{background:rgba(30,30,30,.55);color:var(--white)}
.card.dim p{width:270px;font-size:12px;line-height:20px;text-align:center;margin-bottom:26px}

/* good reads */
.reads{top:3035px;height:411px}
.reads h2{margin-top:53px}
.read{position:absolute;top:140px;width:508px;height:210px;background:#e3e3e3;display:flex}
.read .thumb{width:205px;height:210px;flex:none}
.read .body{padding:20px 22px}
.read h3{font-family:"Montserrat",sans-serif;font-weight:800;font-size:20px;color:#222}
.read h4{font-weight:400;font-size:19px;color:#333;margin-top:2px}
.read p{font-size:14px;line-height:20px;margin-top:12px;color:#333}

/* appointment */
.appt{top:3446px;height:492px}
.appt h2{margin-top:75px}
.field{position:absolute;background:var(--grey);font-family:"Montserrat",sans-serif;font-weight:700;font-size:13px;color:#222;padding:14px 20px}
.appt .note{position:absolute;top:368px;width:1200px;text-align:center;font-size:20px;color:#444}
.appt .btn{position:absolute;top:409px;left:497px;width:206px;height:42px;line-height:42px}

/* map */
.map{top:3938px;height:339px;background:linear-gradient(135deg,#eceae4,#e2e6e0 60%,#dfe5ea)}

/* footer */
.foot{top:4277px;height:277px;display:flex}
.foot-left{width:443px;background:var(--dark);color:var(--white);text-align:center;padding-top:40px}
.foot-left .dot{display:block;width:110px;height:110px;border-radius:50%;background:#2a2a2a;margin:0 auto 16px}
.foot-left .mark{font-family:"Montserrat",sans-serif;font-weight:700;font-size:20px}
.foot-left .sub{font-size:14px;margin-top:40px}
.foot-right{flex:1;background:var(--orange);color:var(--white);padding:55px 0 0 85px;display:flex;gap:130px}
.foot-right h3{font-family:"Montserrat",sans-serif;font-weight:700;font-size:24px;margin-bottom:16px}
.foot-right li{list-style:none;font-size:14px;line-height:27px;display:flex;gap:12px;align-items:flex-start}
.foot-right li svg{margin-top:6px;flex:none}
.foot-right .links li:before{content:"›";font-weight:700}
.bar{top:4554px;height:61px;background:#000;color:var(--white);font-size:12px;display:flex;align-items:center;padding:0 90px}
.bar .legal{width:500px}
.bar .copy{flex:1}
.bar .social{display:flex;gap:30px}
.bar .social i{width:12px;height:12px;border-radius:50%;background:var(--white);display:block}
</style>
</head>
<body>

<header class="hero">
  <div class="hero-bg" role="img" aria-label="Sunset over a rocky coastline with mossy boulders"></div>
  <nav class="nav"><span>HOME</span><span>ABOUT US</span><span>SERVICES</span><span>GOOD READS</span><span>CONTACT US</span></nav>
  <div class="hero-mark"><span class="dot"></span>Halvorsen Serenity</div>
  <div class="hero-name">Dr Halvorsen Serenity Center</div>
  <div class="hero-contact">
    <span><svg width="22" height="22" viewBox="0 0 22 22"><circle cx="11" cy="11" r="10" fill="none" stroke="#fff" stroke-width="2"/><path d="M11 5a4 4 0 0 0-4 4c0 3 4 8 4 8s4-5 4-8a4 4 0 0 0-4-4z" fill="#fff"/></svg>2740 Birchwood Lane, Suite 204, Alder Falls, OH 45901</span>
    <span><svg width="22" height="22" viewBox="0 0 22 22"><circle cx="11" cy="11" r="10" fill="none" stroke="#fff" stroke-width="2"/><path d="M7 6l3 0 1 3-2 1a7 7 0 0 0 3 3l1-2 3 1 0 3c-6 0-9-3-9-9z" fill="#fff"/></svg>(555) 201-0172</span>
    <span><svg width="22" height="22" viewBox="0 0 22 22"><circle cx="11" cy="11" r="10" fill="none" stroke="#fff" stroke-width="2"/><rect x="6" y="7" width="10" height="8" fill="#fff"/><path d="M6 7l5 4 5-4" stroke="#888" fill="none"/></svg>care@halvorsenserenity.com</span>
  </div>
  <div class="hero-arrows">
    <i><svg width="16" height="12"><path d="M15 6H2M6 1L1 6l5 5" stroke="#fff" stroke-width="2" fill="none"/></svg></i>
    <i><svg width="16" height="12"><path d="M1 6h13M10 1l5 5-5 5" stroke="#fff" stroke-width="2" fill="none"/></svg></i>
  </div>
</header>

<section class="welcome">
  <div class="eyebrow">welcome to</div>
  <h2 class="title">DR HALVORSEN SERENITY CENTER</h2>
  <svg class="wave" width="150" height="10" viewBox="0 0 150 10"><path d="M0 5q7.5-6 15 0t15 0 15 0 15 0 15 0 15 0 15 0 15 0 15 0 15 0" stroke="#f26b1d" stroke-width="2" fill="none"/></svg>
  <p class="intro">Each individual is unique with unique personality and unique needs. Therefore we provide individual treatment customized for you or your child. Multiculturalism also informs our practice. We are a full service mental health practice with the capacity to serve adults, children, teens and their parents.</p>
  <p>We provide high quality evidence based treatment and care including medication management, pharmacogenomic testing, individual psychotherapy, group psychotherapy, art therapy, CBT, DBT and trauma therapy. Our providers are experts in treating variety of illnesses such as depression, anxiety, schizophrenia, ADHD, gender identity concerns and PTSD.</p>
  <p>We are experienced in a variety of methods that help people achieve their psychological goals, and we will discuss with you the best ways to attain the health and wellness that you deserve. We are committed to helping you achieve your optimal level of emotional functioning and fulfill a successful life.</p>
</section>

<section class="about">
  <div class="about-bg" role="img" aria-label="Soft sky and sea backdrop over a wooden pier"></div>
  <div class="eyebrow">about us</div>
  <div class="hands" role="img" aria-label="Two hands raised together forming a shape"></div>
  <h2 class="title">ABOUT DR HALVORSEN SERENITY CENTER</h2>
  <div class="about-box">
    <p>You will find a number of highly specialized – experienced and caring therapists and psychiatrists in Serenity Center. We provide medication management and psychotherapy (counseling) across the lifespan.<br><b>– children, teens and adults.</b></p>
    <h4>Other than English, we speak the following languages</h4>
    <div class="langs">Spanish<b></b>German<b></b>Farsi<b></b>Hebrew</div>
  </div>
  <div class="team">
    <div role="img" aria-label="Team member portrait" style="background:linear-gradient(#d8d4cf,#a99a8c)"></div>
    <div role="img" aria-label="Team member portrait" style="background:linear-gradient(#c9c3bb,#9a8070)"></div>
    <div class="active" role="img" aria-label="Portrait of the company CEO" style="background:linear-gradient(#a7a9ad,#6e625a)"></div>
    <div role="img" aria-label="Team member portrait" style="background:linear-gradient(#7a7f7a,#4a3a32)"></div>
    <div role="img" aria-label="Team member portrait" style="background:linear-gradient(#b28c7c,#7a4e44)"></div>
  </div>
  <div class="member">
    <h3>Marcus Ellery</h3>
    <div class="role">Company CEO</div>
    <p>Sed ut perspiciatis unde omnis iste natus error sit voluptatem accusantium doloremque laudantium, totam rem aperiam, eaque ipsa quae ab illo inventore veritatis et quasi architecto beatae vitae dicta sunt explicabo. Nemo enim ipsam voluptatem quia voluptas sit aspernatur aut odit aut fugit,</p>
    <span class="btn">MAKE AN APPOINTMENT</span>
  </div>
</section>

<section class="services">
  <div class="services-bg" role="img" aria-label="Dusky sky above a sandy beach with driftwood"></div>
  <h2 class="title">SERVICES</h2>
  <svg class="wave abs" style="top:88px;left:525px" width="150" height="10" viewBox="0 0 150 10"><path d="M0 5q7.5-6 15 0t15 0 15 0 15 0 15 0 15 0 15 0 15 0 15 0 15 0" stroke="#f26b1d" stroke-width="2" fill="none"/></svg>
  <div class="card" style="top:133px;left:74px;width:323px;height:262px">
    <svg width="80" height="70" viewBox="0 0 80 70" fill="none" stroke="#fff" stroke-width="3"><path d="M10 40l15-10h15l-5 8h-10M70 40L55 30H40"/><path d="M5 45l15 20M75 45L60 65"/><path d="M32 10h16v8h8v16h-8v8H32v-8h-8V18h8z"/></svg>
    <div class="label">MEDICATION MANAGEMENT</div>
  </div>
  <div class="card" style="top:133px;left:440px;width:323px;height:262px">
    <svg width="80" height="80" viewBox="0 0 80 80" fill="none" stroke="#fff" stroke-width="3"><path d="M25 75V58c-10-6-14-16-12-28C16 12 30 5 45 6c16 2 25 14 24 28l6 12h-7v12H52v17"/><path d="M44 32a5 5 0 1 1-5-5 10 10 0 1 1-10 10 15 15 0 1 1 15 15"/></svg>
    <div class="label">PSYCHOTHERAPY</div>
  </div>
  <div class="card dim" style="top:133px;left:806px;width:320px;height:262px">
    <p>Sed ut perspiciatis unde omnis iste natus error sit voluptatem accusantium doloremque laudantium, totam rem aperiam, eaque ipsa quae ab illo inventore veritatis et quasi architecto beatae vitae dicta sunt</p>
    <div class="label">ART THERAPY</div>
  </div>
  <div class="card" style="top:431px;left:74px;width:508px;height:262px">
    <svg width="110" height="80" viewBox="0 0 110 80" fill="none" stroke="#fff" stroke-width="3"><rect x="20" y="35" width="40" height="40" rx="4"/><path d="M40 30c-6-8 0-14 0-22 6 8 6 14 0 22z"/><path d="M65 75c0-20 10-30 30-35-4 20-14 30-30 35zM70 60c8-2 14-8 18-14"/></svg>
    <div class="label">TREATMENT APPROACH</div>
  </div>
  <div class="card" style="top:431px;left:622px;width:504px;height:262px">
    <svg width="90" height="80" viewBox="0 0 90 80" fill="none" stroke="#fff" stroke-width="3"><circle cx="45" cy="22" r="12"/><path d="M25 60c0-14 8-22 20-22s20 8 20 22M15 70h60"/><path d="M10 15l4 4 4-4M72 15l4 4 4-4M10 45l4 4 4-4M72 45l4 4 4-4"/></svg>
    <div class="label">TREATMENT AREAS</div>
  </div>
</section>

<section class="reads">
  <h2 class="title">GOOD READS</h2>
  <svg class="wave" width="150" height="10" viewBox="0 0 150 10"><path d="M0 5q7.5-6 15 0t15 0 15 0 15 0 15 0 15 0 15 0 15 0 15 0 15 0" stroke="#f26b1d" stroke-width="2" fill="none"/></svg>
  <article class="read" style="left:74px">
    <div class="thumb" role="img" aria-label="Stethoscope on a white surface" style="background:linear-gradient(135deg,#f4f6f8,#b8c2cc)"></div>
    <div class="body"><h3>FINIBUS BONORUM ET</h3><h4>Lora dani</h4><p>Sed ut perspiciatis unde omnis iste natus error sit voluptatem accusantium doloremque laudantium, totam rem aperiam, eaque ipsa</p></div>
  </article>
  <article class="read" style="left:618px">
    <div class="thumb" role="img" aria-label="Stacked balancing stones by the water" style="background:linear-gradient(180deg,#8b96a0,#3c4148)"></div>
    <div class="body"><h3>FINIBUS BONORUM ET</h3><h4>Lora dani</h4><p>Sed ut perspiciatis unde omnis iste natus error sit voluptatem accusantium doloremque laudantium, totam rem aperiam, eaque ipsa</p></div>
  </article>
</section>

<section class="appt">
  <h2 class="title">APPOINTMENT REQUEST</h2>
  <svg class="wave" width="150" height="10" viewBox="0 0 150 10"><path d="M0 5q7.5-6 15 0t15 0 15 0 15 0 15 0 15 0 15 0 15 0 15 0 15 0" stroke="#f26b1d" stroke-width="2" fill="none"/></svg>
  <div class="field" style="top:188px;left:197px;width:400px;height:46px">NAME</div>
  <div class="field" style="top:188px;left:609px;width:394px;height:46px">EMAIL</div>
  <div class="field" style="top:246px;left:197px;width:806px;height:99px">MESSAGE</div>
  <div class="note">Please contact me for an appointment</div>
  <span class="btn">SUBMIT</span>
</section>

<section class="map" role="img" aria-label="Street map showing the clinic location"></section>

<footer class="foot">
  <div class="foot-left">
    <span class="dot"></span>
    <div class="mark">Halvorsen Serenity</div>
    <div class="sub">Dr Halvorsen Serenity Center</div>
  </div>
  <div class="foot-right">
    <div>
      <h3>CONTACT INFO</h3>
      <ul>
        <li><svg width="14" height="14" viewBox="0 0 14 14"><path d="M2 1h3l1 3-2 1a7 7 0 0 0 4 4l1-2 3 1v3C6 12 2 8 2 1z" fill="#fff"/></svg>(555) 201-0172</li>
        <li><svg width="14" height="14" viewBox="0 0 14 14"><rect x="1" y="3" width="12" height="8" fill="#fff"/></svg>care@halvorsenserenity.com</li>
        <li><svg width="14" height="14" viewBox="0 0 14 14"><path d="M7 1a4 4 0 0 0-4 4c0 3 4 8 4 8s4-5 4-8a4 4 0 0 0-4-4z" fill="#fff"/></svg>2740 Birchwood Lane, Suite 204,<br>Alder Falls, OH 45901</li>
      </ul>
    </div>
    <div>
      <h3>QUICK LINKS</h3>
      <ul class="links"><li>Home</li><li>About Us</li><li>Services</li><li>Good Reads</li><li>Contact Us</li></ul>
    </div>
  </div>
</footer>

<section class="bar">
  <div class="legal">Terms and conditions &nbsp;|&nbsp; Cookies policy &nbsp;|&nbsp; Privacy policy</div>
  <div class="copy">2019 © www.halvorsenserenity.com</div>
  <div class="social"><i></i><i></i><i></i><i></i><i></i></div>
</section>

</body>
</html>
```